Business Card design for law firm = Brightvale Australia

We are seeking a new design for our business cards.
We are keeping our logo, which is attached.
We need space for
Name
Title
Address is , which is
Level 7
214 Marlowe Street
Sydney NSW 2047
Phone :
Mobile :
Fax :
Email :
DX :
website www.brightvale-example.com.au

Industry/Entity Type

Law Firm / Banking and Finance

Contact Information for Business Card

We are seeking a new design for our business cards. We are keeping our logo. We need space for Name Title Address is Level 7 214 Marlowe Street Sydney NSW 2047 Phone Mobile Fax Email DX website www.brightvale-example.com.au

Colors
0054AA
0677BA
7BADD7
CADEEF
E8F1F8

Requirements
Must have
• see our website for general feel www.brightvale-example.com.au

```html
<!DOCTYPE html>
<html lang="en">
<head>
<meta charset="utf-8">
<title>Brightvale Australia — Business Card</title>
<link rel="stylesheet" href="https://fonts.googleapis.com/css2?family=EB+Garamond:wght@400&display=swap">
<style>
  :root {
    --bg: #2b2b2b;
    --card: #eeeeee;
    --navy: #2a4b9b;
    --teal: #1a8dc4;
    --ink: #2a2a2a;
  }
  * { margin: 0; padding: 0; box-sizing: border-box; }
  html, body { width: 1200px; height: 1138px; overflow: hidden; background: var(--bg); }
  .canvas { position: relative; width: 1200px; height: 1138px; }
  .card {
    position: absolute; width: 622px; height: 376px;
    background: var(--card); border-radius: 16px; overflow: hidden;
    font-family: "EB Garamond", Georgia, serif; color: var(--ink);
  }
  .card--front { left: 272px; top: 184px; }
  .card--back { left: 274px; top: 606px; }

  .company-name {
    position: absolute; left: 0; right: 0; top: 150px; text-align: center;
    font-size: 42px; font-weight: 400; color: var(--navy); line-height: 1;
  }
  .front-web {
    position: absolute; left: 0; right: 0; top: 333px; text-align: center;
    font-size: 15px; letter-spacing: 4.6px; color: var(--ink); white-space: nowrap;
  }
  .front-bar { position: absolute; left: 142px; width: 340px; top: 367px; height: 9px; background: var(--navy); }

  .person { position: absolute; right: 350px; top: 156px; text-align: right; }
  .person__name { font-size: 25px; color: var(--navy); line-height: 1.1; }
  .person__title { font-size: 17px; line-height: 1.2; }
  .contacts { position: absolute; left: 300px; top: 146px; list-style: none; }
  .contacts li { display: flex; align-items: center; height: 20px; font-size: 16px; white-space: nowrap; }
  .contacts svg { width: 14px; height: 14px; margin-right: 12px; fill: var(--teal); flex: none; }
  .address { position: absolute; left: 0; right: 0; top: 322px; text-align: center; font-size: 17px; }
</style>
</head>
<body>
<main class="canvas">
  <section class="card card--front">
    <div class="company-name">Brightvale Australia</div>
    <div class="front-web">www.brightvale-example.com.au</div>
    <div class="front-bar"></div>
  </section>

  <section class="card card--back">
    <div class="person">
      <div class="person__name">Tom Ellery</div>
      <div class="person__title">Managing Director</div>
    </div>
    <ul class="contacts">
      <li><svg viewBox="0 0 14 14"><path d="M1 4c0-2 3-3 6-3s6 1 6 3v1h-3V4H4v1H1z M3 6h8l2 6H1z"/></svg>02 9000 0122</li>
      <li><svg viewBox="0 0 14 14"><path d="M4 1h6v3H4z M1 5h12v6h-2V9H3v2H1z M4 10h6v3H4z"/></svg>02 9000 6411</li>
      <li><svg viewBox="0 0 14 14"><path d="M1 3h12v8H1zM2 4l5 4 5-4M2 10l4-3M12 10l-4-3" fill="none" stroke="#1a8dc4" stroke-width="1.4"/></svg>tom.ellery@brightvale-example.com.au</li>
      <li><svg viewBox="0 0 14 14"><circle cx="7" cy="7" r="5.5" fill="none" stroke="#1a8dc4" stroke-width="1.3"/><path d="M1.5 7h11M7 1.5v11" stroke="#1a8dc4" stroke-width="1" fill="none"/><ellipse cx="7" cy="7" rx="2.5" ry="5.5" fill="none" stroke="#1a8dc4" stroke-width="1"/></svg>www.brightvale-example.com.au</li>
    </ul>
    <div class="address">Level 7 214 Marlowe Street Sydney NSW 2047</div>
  </section>
</main>
</body>
</html>
```